Construction material supplies company business card ****

1. Full company name “K T Masonry Works Ltd”
I am after a Business card design for the company as a whole. We are better known in Solomon Islands as “K T Masonry” for short.

We are a building materials supplier of
Ready Mixed Concrete, Bricks and Blocks,
Quarry products- gravel, aggregates, sand etc.
Cement distributor/retailer of reputable brands.
Other prefab concrete products. Culverts, wave breakers, concrete retaining blocks etc.

2. Competitive Advantage over Competition: Quality, efficient, professional, dependable, reliable

3. We want people to feel trust worthy, high quality, strong when they see our brand

5. No preference to color. Maybe more sturdy and corporate. Not fancy.

Industry/Entity Type

CONSTRUCTION SUPPLY

Contact Information for Business Card

Name, Position, office phone mob phone, email

Requirements
Must have
• the company logo
Nice to have
• would like to see a mixture of designs, of with logo only and also with simple graphic designs to bring out the company whilst still have the strong sturdy professional feeling

```html
<!DOCTYPE html>
<html lang="en">
<head>
<meta charset="utf-8">
<title>K T Masonry – Business Card</title>
<link href="https://fonts.googleapis.com/css2?family=Orbitron:wght@600&family=Roboto:wght@400;500&display=swap" rel="stylesheet">
<style>
  :root {
    --backdrop: #2a2a2a;
    --concrete-light: #efefef;
    --concrete-mid: #dcdcdc;
    --concrete-dark: #cfcfcf;
    --navy: #0b3a5c;
    --emboss: #b4b4b4;
  }
  html, body {
    margin: 0;
    width: 1200px;
    height: 1138px;
    overflow: hidden;
    background: var(--backdrop);
  }
  .card {
    position: absolute;
    left: 275px;
    width: 621px;
    height: 374px;
    border-radius: 16px;
    overflow: hidden;
    background: radial-gradient(ellipse at 30% 30%, var(--concrete-light), var(--concrete-mid) 70%, var(--concrete-dark));
    font-family: "Roboto", sans-serif;
    color: var(--navy);
  }
  .card--front { top: 186px; }
  .card--back { top: 608px; }

  .front-mark {
    position: absolute;
    left: 0; right: 0;
    top: 150px;
    display: flex;
    justify-content: center;
    align-items: center;
    gap: 14px;
  }
  .front-mark__square {
    width: 22px; height: 22px;
    background: var(--emboss);
  }
  .front-mark__name {
    font-family: "Orbitron", sans-serif;
    font-weight: 600;
    font-size: 34px;
    color: var(--emboss);
    letter-spacing: 1px;
  }
  .front-url {
    position: absolute;
    left: 0; right: 0;
    top: 332px;
    text-align: center;
    font-size: 15px;
    letter-spacing: 6.5px;
  }

  .brand-name {
    position: absolute;
    left: 30px; top: 46px;
    margin: 0;
    font-family: "Orbitron", sans-serif;
    font-weight: 600;
    font-size: 28px;
    letter-spacing: 0.5px;
  }
  .person {
    position: absolute;
    left: 30px; top: 140px;
  }
  .person__name {
    margin: 0;
    font-size: 22px;
    font-weight: 500;
  }
  .person__role {
    margin: 3px 0 0;
    font-size: 15.5px;
  }
  .contacts {
    position: absolute;
    left: 30px; top: 225px;
    margin: 0; padding: 0;
    list-style: none;
    font-size: 16px;
  }
  .contacts li {
    display: flex;
    align-items: center;
    height: 26px;
  }
  .contacts svg {
    width: 14px; height: 14px;
    margin-right: 18px;
    fill: var(--navy);
  }
  .address {
    position: absolute;
    left: 30px; top: 304px;
    margin: 0;
    font-size: 16px;
    font-style: normal;
    line-height: 26px;
  }
  .brand-block {
    position: absolute;
    right: 0; top: 62px;
    width: 250px; height: 250px;
    background: var(--navy);
  }
</style>
</head>
<body>
  <section class="card card--front">
    <div class="front-mark">
      <span class="front-mark__square"></span>
      <span class="front-mark__name">K T MASONRY</span>
    </div>
    <div class="front-url">www.ktmasonry.com</div>
  </section>

  <section class="card card--back">
    <h1 class="brand-name">K T MASONRY</h1>
    <div class="person">
      <p class="person__name">Daniel Harper</p>
      <p class="person__role">Managing Director</p>
    </div>
    <ul class="contacts">
      <li>
        <svg viewBox="0 0 16 16" aria-hidden="true"><path d="M3 2h3l1.5 3.5-2 1.2a9 9 0 0 0 3.8 3.8l1.2-2L14 10v3a1 1 0 0 1-1 1A11 11 0 0 1 2 3a1 1 0 0 1 1-1z"/></svg>
        000 0000 0000
      </li>
      <li>
        <svg viewBox="0 0 16 16" aria-hidden="true"><path d="M1 3h14v10H1z M2 4.5v.4l6 4 6-4v-.4z" fill-rule="evenodd"/></svg>
        daniel@ktmasonry.com
      </li>
      <li>
        <svg viewBox="0 0 16 16" aria-hidden="true"><path d="M8 1a7 7 0 1 0 0 14A7 7 0 0 0 8 1zm0 1.3c.8.8 1.5 2.3 1.7 4.2H6.3C6.5 4.6 7.2 3.1 8 2.3zM5 6.5H2.4A5.7 5.7 0 0 1 6 2.6 9 9 0 0 0 5 6.5zm0 1.3a9 9 0 0 0 1 3.9 5.7 5.7 0 0 1-3.6-3.9zm1.3 0h3.4c-.2 1.9-.9 3.4-1.7 4.2-.8-.8-1.5-2.3-1.7-4.2zm4.7 0h2.6a5.7 5.7 0 0 1-3.6 3.9 9 9 0 0 0 1-3.9zm0-1.3a9 9 0 0 0-1-3.9 5.7 5.7 0 0 1 3.6 3.9z"/></svg>
        www.ktmasonry.com
      </li>
    </ul>
    <address class="address">18 Harbour Road, Point Cruz,<br>Honiara, SB 00120</address>
    <div class="brand-block"></div>
  </section>
</body>
</html>
```